Brightwave Reach - Business Card

We need a business card for a Social Media Marketing company that specializes in online marketing for small businesses in Canada using common Social Media platforms such as Pixlora, Chatterly, Blinkpost & Quibber.

I have uploaded a copy of our logo which I would like utilized in the business card. We would like the business card to be modern yet classy design.

Our website is www.brightwavereach.ca

Industry/Entity Type

Marketing

Contact Information for Business Card

Email: info@brightwavereach.ca
Website: www.brightwavereach.ca
Telephone: 604-555-0193

Colors

Designer to choose colors to be used in the design.

Requirements
Must have
• Social Media icons on reverse
• Please add some designs with color.

```html
<!DOCTYPE html>
<html lang="en">
<head>
<meta charset="utf-8">
<title>Brightwave Reach – Business Card</title>
<link href="https://fonts.googleapis.com/css2?family=Oswald:wght@500;700&family=Roboto:wght@300;400&display=swap" rel="stylesheet">
<style>
  :root {
    --bg: #e6e6e6;
    --card-dark: #3b3e40;
    --card-light: #f4f4f4;
    --ink: #333537;
    --ink-soft: #9a9c9e;
    --on-dark: #f1f1f1;
    --line-dark: #8a8d90;
  }
  * { margin: 0; padding: 0; box-sizing: border-box; }
  html, body { width: 1200px; height: 886px; overflow: hidden; background: var(--bg); }
  .canvas { position: relative; width: 1200px; height: 886px; }
  .card {
    position: absolute; left: 320px; width: 560px; height: 320px;
    box-shadow: 0 6px 18px rgba(0,0,0,.18);
  }
  .card--back { top: 100px; background: var(--card-dark); color: var(--on-dark); }
  .card--front { top: 466px; background: var(--card-light); color: var(--ink); }

  /* Back */
  .back-logo {
    position: absolute; left: 90px; top: 110px; width: 260px;
    display: flex; align-items: center; gap: 12px;
  }
  .back-logo__mark { width: 18px; height: 18px; border: 2px solid var(--on-dark); flex: none; }
  .back-logo__name {
    font-family: "Oswald", sans-serif; font-weight: 700; font-size: 34px;
    line-height: 1; text-transform: uppercase; letter-spacing: 1px; color: var(--on-dark);
  }
  .social-rail {
    position: absolute; left: 430px; top: 40px; height: 240px; width: 120px;
  }
  .social-rail__line { position: absolute; left: 14px; width: 1px; background: var(--line-dark); }
  .social-rail__line--top { top: 0; height: 70px; }
  .social-rail__line--bottom { bottom: 0; height: 70px; }
  .social-list {
    position: absolute; top: 78px; left: 0; list-style: none;
    display: flex; flex-direction: column; gap: 8px;
  }
  .social-list li {
    display: flex; align-items: center; gap: 8px;
    font-family: "Roboto", sans-serif; font-weight: 400; font-size: 11px; color: var(--on-dark);
  }
  .social-list .dot { width: 20px; height: 20px; border: 1.5px solid var(--on-dark); border-radius: 50%; flex: none; margin-left: 4px; }

  /* Front */
  .frame { position: absolute; inset: 10px; border: 2px solid var(--ink); }
  .frame::after { content: ""; position: absolute; inset: 4px; border: 1px solid var(--ink); }
  .front-logo {
    position: absolute; left: 40px; top: 36px;
    font-family: "Oswald", sans-serif; font-weight: 700; font-size: 26px;
    line-height: 1; text-transform: uppercase; letter-spacing: 1px; color: var(--ink);
  }
  .person { position: absolute; left: 40px; top: 120px; }
  .person__icon { display: block; margin-bottom: 8px; }
  .person__name {
    font-family: "Oswald", sans-serif; font-weight: 500; font-size: 26px;
    text-transform: uppercase; line-height: 1; letter-spacing: .5px;
  }
  .person__role {
    font-family: "Roboto", sans-serif; font-weight: 300; font-size: 13px;
    color: var(--ink-soft); text-transform: uppercase; letter-spacing: .6px; margin-top: 6px;
  }
  .contacts {
    position: absolute; left: 290px; top: 112px; list-style: none;
    display: flex; flex-direction: column; gap: 16px;
    font-family: "Roboto", sans-serif; font-weight: 400; font-size: 13px;
  }
  .contacts li { display: flex; align-items: center; gap: 10px; }
  .contacts svg { flex: none; }
  .leaf-art {
    position: absolute; right: 40px; bottom: 34px; width: 44px; height: 44px;
    border-radius: 50%; background: radial-gradient(circle, #5a5c5e, #8c8e90);
  }
</style>
</head>
<body>
<main class="canvas">
  <section class="card card--back" aria-label="Card back">
    <div class="back-logo">
      <span class="back-logo__mark"></span>
      <span class="back-logo__name">Brightwave Reach</span>
    </div>
    <div class="social-rail">
      <span class="social-rail__line social-rail__line--top"></span>
      <ul class="social-list">
        <li><span class="dot"></span>Chatterly</li>
        <li><span class="dot"></span>Pixlora</li>
        <li><span class="dot"></span>Quibber</li>
      </ul>
      <span class="social-rail__line social-rail__line--bottom"></span>
    </div>
  </section>

  <section class="card card--front" aria-label="Card front">
    <div class="frame"></div>
    <div class="front-logo">Brightwave<br>Reach</div>
    <div class="person">
      <svg class="person__icon" width="18" height="18" viewBox="0 0 18 18" aria-hidden="true">
        <circle cx="9" cy="5" r="4" fill="var(--ink)"/>
        <path d="M1 18c0-5 3.5-7 8-7s8 2 8 7z" fill="var(--ink)"/>
      </svg>
      <div class="person__name">Daniel Hartley</div>
      <div class="person__role">CEO/Founder</div>
    </div>
    <ul class="contacts">
      <li>
        <svg width="14" height="14" viewBox="0 0 14 14" aria-hidden="true"><path d="M3 1l2 3-1.5 1.5a8 8 0 0 0 5 5L10 9l3 2-1.5 2.5C6 13 1 8 .5 2.5z" fill="var(--ink)"/></svg>
        <span>604-555-0193</span>
      </li>
      <li>
        <svg width="14" height="12" viewBox="0 0 14 12" aria-hidden="true"><rect x="1" y="1" width="12" height="10" fill="var(--ink)"/><path d="M1 1l6 5 6-5" stroke="var(--card-light)" fill="none"/></svg>
        <span>info@brightwavereach.ca</span>
      </li>
      <li>
        <svg width="14" height="14" viewBox="0 0 14 14" aria-hidden="true"><circle cx="7" cy="7" r="6" fill="var(--ink)"/><path d="M1 7h12M7 1c-3 3-3 9 0 12M7 1c3 3 3 9 0 12" stroke="var(--card-light)" fill="none" stroke-width=".8"/></svg>
        <span>www.brightwavereach.ca</span>
      </li>
    </ul>
    <div class="leaf-art" role="img" aria-label="Grey textured maple leaf motif"></div>
  </section>
</main>
</body>
</html>
```